Brevanel Capital LLC

Need Professional Business cards for New Investment Fund

Target Market(s)

High Quality investors

Industry/Entity Type

Financial

Contact Information for Business Card

Phone Number +1 555 284 6190
Name Lukas Varenko
Title Fund Manager
email lv@FundBrevanel.com
Website www.FundBrevanel.com

Colors

Designer to choose colors to be used in the design.

Requirements
Must have
• Must have our Logo and all of the above. Must be made so lettering and loge can be raised

```html
<!DOCTYPE html>
<html lang="en">
<head>
<meta charset="UTF-8">
<title>Brevanel Capital LLC — Business Card</title>
<link rel="stylesheet" href="https://fonts.googleapis.com/css2?family=Jost:wght@500;600&family=Raleway:wght@400;500&display=swap">
<style>
  :root {
    --stage: #262626;
    --green: #59b94a;
    --card-dark: #131417;
    --white: #ffffff;
    --soft-white: #e9e9e9;
  }
  * { box-sizing: border-box; margin: 0; padding: 0; }
  html, body { width: 1200px; height: 900px; overflow: hidden; }
  body {
    background: var(--stage);
    font-family: "Raleway", sans-serif;
    position: relative;
  }
  .card {
    position: absolute;
    left: 270px;
    width: 660px;
    height: 377px;
    border-radius: 3px;
    overflow: hidden;
  }
  .card--front { top: 50px; background: var(--green); }
  .card--back { top: 470px; background: var(--card-dark); }

  .brand-name {
    font-family: "Jost", sans-serif;
    font-weight: 600;
    letter-spacing: 3px;
    text-transform: uppercase;
    white-space: nowrap;
  }
  .front-mark {
    position: absolute;
    inset: 0;
    display: flex;
    align-items: center;
    justify-content: center;
    gap: 16px;
  }
  .front-mark .mark-square {
    width: 34px; height: 34px; background: var(--white);
  }
  .front-mark .brand-name { font-size: 46px; color: var(--white); }

  .back-mark {
    position: absolute;
    right: 48px;
    top: 64px;
    display: flex;
    align-items: center;
    gap: 10px;
  }
  .back-mark .mark-square { width: 18px; height: 18px; background: var(--green); }
  .back-mark .brand-name { font-size: 26px; color: var(--white); }

  .accent-bar {
    position: absolute; left: 28px; top: 196px;
    width: 10px; height: 40px; background: var(--green);
  }
  .divider {
    position: absolute; left: 80px; right: 40px; top: 186px;
    height: 2px; background: var(--green);
  }
  .holder {
    position: absolute; left: 80px; top: 202px;
  }
  .holder-name {
    font-family: "Jost", sans-serif;
    font-weight: 600;
    font-size: 25px;
    letter-spacing: 1.5px;
    text-transform: uppercase;
    color: var(--white);
    white-space: nowrap;
  }
  .holder-title {
    font-size: 18px;
    color: var(--soft-white);
    margin-top: 2px;
    white-space: nowrap;
  }
  .contacts {
    position: absolute; right: 40px; bottom: 34px;
    list-style: none;
    text-align: right;
  }
  .contacts li {
    display: flex; align-items: center; justify-content: flex-end;
    gap: 14px;
    font-size: 19px;
    color: var(--white);
    line-height: 32px;
    white-space: nowrap;
  }
  .contacts svg { width: 18px; height: 18px; flex: none; }
</style>
</head>
<body>
  <section class="card card--front" aria-label="Card front">
    <div class="front-mark">
      <span class="mark-square"></span>
      <span class="brand-name">Brevanel</span>
    </div>
  </section>

  <section class="card card--back" aria-label="Card back">
    <div class="back-mark">
      <span class="mark-square"></span>
      <span class="brand-name">Brevanel</span>
    </div>
    <div class="divider"></div>
    <div class="accent-bar"></div>
    <div class="holder">
      <p class="holder-name">Lukas Varenko</p>
      <p class="holder-title">Title Fund Manager</p>
    </div>
    <ul class="contacts">
      <li>+1 555 284 6190
        <svg viewBox="0 0 24 24" aria-hidden="true"><path fill="#59b94a" d="M6.6 10.8a15 15 0 0 0 6.6 6.6l2.2-2.2a1 1 0 0 1 1-.25 11.4 11.4 0 0 0 3.6.57 1 1 0 0 1 1 1V20a1 1 0 0 1-1 1A17 17 0 0 1 3 4a1 1 0 0 1 1-1h3.5a1 1 0 0 1 1 1c0 1.25.2 2.45.57 3.57a1 1 0 0 1-.25 1z"/></svg>
      </li>
      <li>lv@FundBrevanel.com
        <svg viewBox="0 0 24 24" aria-hidden="true"><rect x="2.5" y="5" width="19" height="14" rx="1.5" fill="none" stroke="#59b94a" stroke-width="2"/><path d="M3 6l9 7 9-7" fill="none" stroke="#59b94a" stroke-width="2"/></svg>
      </li>
      <li>www.FundBrevanel.com
        <svg viewBox="0 0 24 24" aria-hidden="true"><g fill="none" stroke="#59b94a" stroke-width="1.8"><circle cx="12" cy="12" r="9.5"/><ellipse cx="12" cy="12" rx="4.5" ry="9.5"/><path d="M2.5 12h19M4 7h16M4 17h16"/></g></svg>
      </li>
    </ul>
  </section>
</body>
</html>
```